Sparkling Wine Label Mirren Hollow

Super Premium Sparkling Wine Label

We are a super premium tasmanian fine wine producer and are about to release our first Sparking Wine.

please visit www.mirrenhollow-example.com.au to check out our range of wine. We need a label that will sit within this branding but as the aspirational product. We think that the Vosse grey/navy label will fit into this concept. It is masculine clean elegent and very smick,
and would be a great addition to our line see Argent Pinot Noir label.

However you can be quite creative with Sparkling Line eg Belvane Royal Cuvee is a stunning classical french label featuring gold baroque detail and feminine elegence.

Its up to you if you where spending $50 on a special bottles of sparkling wine what would you expect to see?

Black/Gold Graphite/Gold

Needs a neck /collar label

Main Front Label
Mirren Hollow
Chardonnay Pinot Noir
Tasmania

Back label has all the techical into you can use the back label from existing labels but reverserve out the colours to black and white or graphite and white

We want a label that oozes quality and expense. That says this the way I want to celebrate.

Target Market(s)

40 60 age group appreciator of quality

Industry/Entity Type

Product

Requirements
Must have
• Neck label
Simular to Vosse Shield so
MIRREN arched above
G rondel in middle possibiliy replacing coat of arms
TASMANIA arched under in red

Main Front Label
Mirren Hollow
Tasmania
Chardonnay Pinot Noir 750ML

Back Label / use the attachment Mirren label just reverse out so that it is a black label with white writing and amend information
Mirren Hollow
23 Pell Morrow Rd Ashvale
Tasmania, 7261
0412557390
www.mirrenhollow-example.com.au
contact@mirrenhollow-example.com.au
Sulphur Dioxide Added
Alc/Vol 12.5%
7.7 Standard Drinks

Rondel g

```html
<!DOCTYPE html>
<html lang="en">
<head>
<meta charset="utf-8">
<title>Mirren Hollow Sparkling – Label Set</title>
<link href="https://fonts.googleapis.com/css2?family=Pinyon+Script&family=Libre+Baskerville&family=Raleway:wght@400&family=PT+Sans&display=swap" rel="stylesheet">
<style>
  :root {
    --backdrop: #ece5da;
    --label-black: #0b0b0b;
    --neck-black: #141414;
    --gold: #d9b640;
    --gold-soft: #b8962e;
    --tasmania-red: #c4202a;
    --paper-white: #f2f2f2;
    --map-grey: #1e1e1e;
  }
  html, body {
    margin: 0;
    width: 1200px;
    height: 1133px;
    overflow: hidden;
    background: var(--backdrop);
  }
  .canvas { position: relative; width: 1200px; height: 1133px; }

  .neck-set { position: absolute; top: 170px; width: 240px; height: 470px; }
  .neck-set--front { left: 262px; }
  .neck-set--back { left: 707px; }

  .neck-script {
    font-family: "Pinyon Script", cursive;
    font-size: 54px;
    fill: var(--gold);
  }
  .collar-name {
    font-family: "Libre Baskerville", serif;
    font-size: 15px;
    letter-spacing: 2px;
    fill: var(--gold);
  }
  .collar-region {
    font-family: "Libre Baskerville", serif;
    font-size: 8px;
    letter-spacing: 1px;
    fill: var(--tasmania-red);
  }

  .label {
    position: absolute;
    top: 810px;
    height: 202px;
    background: var(--label-black);
    border: 2px solid var(--gold);
    box-sizing: border-box;
    overflow: hidden;
  }
  .label::before {
    content: "";
    position: absolute;
    inset: 4px;
    border: 1px solid var(--gold);
    pointer-events: none;
  }
  .label--front { left: 264px; width: 236px; }
  .label--back { left: 726px; width: 202px; }

  .front-name {
    position: absolute;
    top: 14px; left: 0; right: 0;
    text-align: center;
    font-family: "Pinyon Script", cursive;
    font-size: 68px;
    line-height: 1;
    color: var(--gold);
    white-space: nowrap;
  }
  .front-subname {
    position: absolute;
    top: 100px; left: 0; right: 0;
    text-align: center;
    padding-left: 40px;
    font-family: "Raleway", sans-serif;
    font-size: 14px;
    letter-spacing: 0.5px;
    color: var(--gold);
  }
  .front-variety {
    position: absolute;
    top: 136px; left: 0; right: 0;
    text-align: center;
    font-family: "Pinyon Script", cursive;
    font-size: 19px;
    color: var(--gold);
    white-space: nowrap;
  }
  .front-footer {
    position: absolute;
    left: 16px; right: 18px; bottom: 12px;
    display: flex;
    justify-content: space-between;
    font-family: "Libre Baskerville", serif;
    font-size: 12px;
    color: var(--paper-white);
  }

  .back-details {
    position: absolute;
    top: 12px; left: 12px; right: 12px;
    font-family: "PT Sans", sans-serif;
    font-size: 6.4px;
    line-height: 8.4px;
    color: var(--paper-white);
    margin: 0;
    font-style: normal;
    white-space: nowrap;
  }
  .back-map {
    position: absolute;
    top: 96px; right: 11px;
    width: 80px; height: 84px;
    background: linear-gradient(160deg, #2a2a2a, var(--map-grey) 60%, #111);
  }
  .back-mark {
    position: absolute;
    left: 12px; top: 116px;
    display: flex; align-items: center; gap: 5px;
  }
  .back-mark__circle {
    width: 34px; height: 34px;
    border: 1px solid var(--paper-white);
    border-radius: 50%;
    box-sizing: border-box;
  }
  .back-mark__name {
    font-family: "PT Sans", sans-serif;
    font-size: 6.4px;
    color: var(--paper-white);
    white-space: nowrap;
  }
  .back-origin {
    position: absolute;
    left: 12px; bottom: 10px;
    font-family: "Libre Baskerville", serif;
    font-size: 8.5px;
    color: var(--paper-white);
    white-space: nowrap;
  }
</style>
</head>
<body>
<main class="canvas">

  <svg class="neck-set neck-set--front" viewBox="0 0 240 470" aria-label="Neck and collar label">
    <defs>
      <path id="arc-top-front" d="M84,392 A36,36 0 0 1 156,392"/>
      <path id="arc-bottom-front" d="M90,392 A30,30 0 0 0 150,392"/>
    </defs>
    <g role="img" aria-label="Black damask pattern on the neck label">
      <path d="M62,6 L178,6 L192,342 L48,342 Z" fill="var(--neck-black)"/>
    </g>
    <line x1="62" y1="6" x2="178" y2="6" stroke="var(--gold)" stroke-width="3"/>
    <text class="neck-script" transform="translate(132,184) rotate(90)" text-anchor="middle">Mirren</text>
    <path class="collar" d="M48,342 L192,342 L220,420 L160,420 Q132,428 120,462 Q108,428 80,420 L20,420 Z"
          fill="var(--label-black)" stroke="var(--gold)" stroke-width="2"/>
    <circle cx="120" cy="392" r="22" fill="none" stroke="var(--gold)" stroke-width="1.5"/>
    <text class="collar-name"><textPath href="#arc-top-front" startOffset="50%" text-anchor="middle">MIRREN</textPath></text>
    <text class="collar-region" dy="8"><textPath href="#arc-bottom-front" startOffset="50%" text-anchor="middle">TASMANIA</textPath></text>
  </svg>

  <svg class="neck-set neck-set--back" viewBox="0 0 240 470" aria-label="Neck and collar label, reverse">
    <defs>
      <path id="arc-top-back" d="M84,392 A36,36 0 0 1 156,392"/>
      <path id="arc-bottom-back" d="M90,392 A30,30 0 0 0 150,392"/>
    </defs>
    <g role="img" aria-label="Black damask pattern on the neck label">
      <path d="M62,6 L178,6 L192,342 L48,342 Z" fill="var(--neck-black)"/>
    </g>
    <line x1="62" y1="6" x2="178" y2="6" stroke="var(--gold)" stroke-width="3"/>
    <path class="collar" d="M48,342 L192,342 L220,420 L160,420 Q132,428 120,462 Q108,428 80,420 L20,420 Z"
          fill="var(--label-black)" stroke="var(--gold)" stroke-width="2"/>
    <circle cx="120" cy="392" r="22" fill="none" stroke="var(--gold)" stroke-width="1.5"/>
    <text class="collar-name"><textPath href="#arc-top-back" startOffset="50%" text-anchor="middle">MIRREN</textPath></text>
    <text class="collar-region" dy="8"><textPath href="#arc-bottom-back" startOffset="50%" text-anchor="middle">TASMANIA</textPath></text>
  </svg>

  <section class="label label--front" aria-label="Front label">
    <div class="front-name">Mirren</div>
    <div class="front-subname">HOLLOW</div>
    <div class="front-variety">Chardonnay Pinot Noir</div>
    <div class="front-footer"><span>750ml</span><span>Tasmania</span></div>
  </section>

  <section class="label label--back" aria-label="Back label">
    <address class="back-details">
      Mirren Hollow<br>
      23 Pell Morrow Road Ashvale<br>
      Tasmania Australia 7261<br>
      0412 557 390<br>
      contact@mirrenhollow-example.com.au<br>
      www.mirrenhollow-example.com.au<br>
      Alc/Vol 12.5 Standard drinks 8<br>
      Sulphur Dioxide added<br>
      7.7 Standard Drinks
    </address>
    <div class="back-map" role="img" aria-label="Map of the East Coast region of Tasmania showing the estate location"></div>
    <div class="back-mark">
      <span class="back-mark__circle"></span>
      <span class="back-mark__name">Mirren Hollow</span>
    </div>
    <div class="back-origin">Wine of Australia</div>
  </section>

</main>
</body>
</html>
```